Business Card Design Project

This is the first time we use our new logo. We need a business card that we can use both on our institutional corporate relationships and also that works for our staff that deals with consumers directly.

VELUNDA is a new company dedicated to empower consumers and to provide them with the best choices for specialized health care using the latest telemedicine technology (medicine at a distance via videoconference).

We want to print this cards in high quality materials and process. We will like designs that allow us to use UV spot varnish and other techniques that will differentiate us.

We are including Two different versions of Color logos. In addition we are including white over black background logos. Those can be used replacing the black for a color.

Please note this is the first time we will be creating any corporate materials with our new logo and colors.

Target Market(s)

34+ consumers of medium high and high socioeconomic levels.

Industry/Entity Type

Health

Requirements
Must have
• Our logo on its original colors
Should not have
• Any other graphical element or design that is not our logo

```html
<!DOCTYPE html>
<html lang="en">
<head>
<meta charset="utf-8">
<title>VELUNDA Business Card</title>
<link rel="stylesheet" href="https://fonts.googleapis.com/css2?family=Questrial&family=Arimo:wght@400;700&display=swap">
<style>
  :root {
    --backdrop: #d9d4ce;
    --card-black: #0d0d0e;
    --card-grey: #26272a;
    --band-blue: #1c5a8c;
    --line-blue: #4fb0e2;
    --mark-blue: #1f6199;
    --mark-teal: #14a39a;
    --text-white: #f4f6f8;
    --divider: #6b6d72;
  }
  html, body {
    margin: 0;
    width: 1200px;
    height: 1057px;
    overflow: hidden;
    background: var(--backdrop);
  }
  .canvas {
    position: relative;
    width: 1200px;
    height: 1057px;
  }
  .card {
    position: absolute;
    width: 760px;
    height: 434px;
    border-radius: 4px;
    overflow: hidden;
    box-shadow: 0 10px 28px rgba(0,0,0,0.35);
    background: linear-gradient(160deg, var(--card-grey) 0%, var(--card-black) 55%, var(--card-grey) 100%);
  }
  .card--front { left: 120px; top: 70px; }
  .card--back { left: 320px; top: 553px; }
  .card svg { display: block; width: 760px; height: 434px; }
  .wordmark { font-family: "Questrial", sans-serif; }
  .body-text { font-family: "Arimo", sans-serif; }
</style>
</head>
<body>
<main class="canvas">

  <section class="card card--front" aria-label="Card front">
    <svg viewBox="0 0 760 434" xmlns="http://www.w3.org/2000/svg">
      <!-- name band -->
      <path class="band" fill="var(--band-blue)"
            d="M0,395 C250,330 480,300 760,160 L760,205 C560,300 330,390 150,434 L0,434 Z"/>
      <path class="band-edge" fill="none" stroke="var(--line-blue)" stroke-width="3"
            d="M0,386 C250,320 480,290 760,150"/>
      <path class="band-edge" fill="none" stroke="var(--line-blue)" stroke-width="2"
            d="M150,434 C330,392 560,302 760,212"/>

      <!-- brand -->
      <circle class="brand-dot" cx="150" cy="140" r="38" fill="var(--mark-teal)"/>
      <text class="wordmark" x="208" y="162" font-size="58" letter-spacing="4" fill="var(--mark-blue)">VELUNDA</text>

      <!-- address -->
      <g class="body-text address" fill="var(--text-white)" font-size="18" text-anchor="end">
        <text x="332" y="232">Street Name</text>
        <text x="332" y="258">City Name</text>
        <text x="332" y="284">State, City Zip Code</text>
      </g>

      <line class="divider" x1="356" y1="206" x2="356" y2="296" stroke="var(--divider)" stroke-width="1.5"/>

      <!-- contacts -->
      <g class="contact-icons" fill="none" stroke="var(--text-white)" stroke-width="1.4">
        <circle cx="382" cy="209" r="6"/>
        <path d="M379,206 q0,6 6,6" />
        <circle cx="382" cy="234" r="6"/>
        <path d="M379,231 q0,6 6,6" />
        <rect x="376" y="254" width="12" height="9"/>
        <path d="M376,254 l6,5 l6,-5"/>
        <circle cx="382" cy="283" r="6"/>
        <ellipse cx="382" cy="283" rx="2.5" ry="6"/>
        <line x1="376" y1="283" x2="388" y2="283"/>
      </g>
      <g class="body-text contacts" fill="var(--text-white)" font-size="17">
        <text x="396" y="215">012-555-0147</text>
        <text x="396" y="240">012-555-0147</text>
        <text x="396" y="265">name@velunda.com</text>
        <text x="396" y="290">www.velunda.com</text>
      </g>

      <!-- holder name -->
      <text class="body-text holder" x="70" y="408" transform="rotate(-12 70 408)" fill="var(--text-white)">
        <tspan font-size="26" font-weight="700">Your Name</tspan><tspan font-size="20">, Title</tspan>
      </text>
    </svg>
  </section>

  <section class="card card--back" aria-label="Card back">
    <svg viewBox="0 0 760 434" xmlns="http://www.w3.org/2000/svg">
      <circle class="brand-dot" cx="180" cy="190" r="34" fill="var(--mark-teal)"/>
      <text class="wordmark" x="400" y="214" text-anchor="middle" font-size="74" letter-spacing="5" fill="var(--mark-blue)">VELUNDA</text>
      <text class="body-text web" x="380" y="336" text-anchor="middle" font-size="26" letter-spacing="7" fill="var(--line-blue)">www.velunda.com</text>
    </svg>
  </section>

</main>
</body>
</html>
```